Anzeigengestaltung für Unternehmensberatung für Pflegedienste
Zielgruppe
Wir sind eine Unternehmensberatung für Pflegedienste. Es soll eine Werbeanzeige erstellt werden, mit welcher schlecht laufende Pflegedienste, die gerade in einer Krise stecken angesprochen werden,
Der slogan soll einfach klingen : Pflege neu gedaxht: wirtschaftlich, nachhaltig, zukunftssicher
Anzeige in 3 Formaten
1. Format 55.3 mm x 118 mm
2. Format 1/ halbe Seite Quer 176 x 118 mm un
3. Format d 1 x A4 _Seite
Der Name der Firma Tolvek GmbH info at tolvek-beispiel.de Tel 0555 91827364 aus Rostock Berlin und bundesweit tätig
Aufgabenstellung
Kreativ und elegant

```html
<!DOCTYPE html>
<html lang="de">
<head>
<meta charset="utf-8">
<title>Tolvek – Anzeigen in drei Formaten</title>
<link href="https://fonts.googleapis.com/css2?family=Cinzel:wght@500&family=EB+Garamond:wght@400&family=Quicksand:wght@500&display=swap" rel="stylesheet">
<style>
  :root{
    --board:#9b9b9b;
    --navy:#1d2650;
    --orange:#ff7300;
    --slate:#7487a5;
    --ink:#f5f5f8;
    --photo-light:#ecebe8;
    --photo-mid:#cdbfae;
    --photo-warm:#a07f64;
  }
  *{margin:0;padding:0;box-sizing:border-box}
  html,body{width:1200px;height:890px;overflow:hidden;background:var(--board)}
  .board{position:relative;width:1200px;height:890px}
  .ad{position:absolute;background:var(--navy);overflow:hidden;color:var(--ink)}
  .ad-a4{left:41px;top:32px;width:584px;height:826px}
  .ad-tall{left:843px;top:32px;width:151px;height:321px}
  .ad-wide{left:679px;top:537px;width:480px;height:321px}
  .shapes{position:absolute;left:0;top:0}
  .photo{position:absolute;background:linear-gradient(100deg,var(--photo-light) 0%,var(--photo-mid) 45%,var(--photo-warm) 75%,var(--photo-light) 100%)}
  .brand{position:absolute;font-family:"Cinzel",serif;font-weight:500;color:var(--slate);text-align:center;line-height:1;letter-spacing:.04em}
  .headline{position:absolute;text-align:center;font-family:"Quicksand",sans-serif;font-weight:500}
  .headline .title{display:block}
  .headline .sub{display:block}
  .pitch{position:absolute;text-align:center;font-family:"EB Garamond",serif;font-weight:400}
  .contact{position:absolute;font-family:"Quicksand",sans-serif;font-weight:500;text-align:center}
  .contact .row{display:flex;justify-content:center;align-items:center;gap:.9em}
  .contact .item{display:inline-flex;align-items:center;gap:.2em;white-space:nowrap}
  .contact svg{fill:var(--ink);flex:none}

  /* A4 */
  .ad-a4 .brand{left:0;top:30px;width:584px;font-size:50px}
  .ad-a4 .photo{left:61px;top:100px;width:469px;height:330px}
  .ad-a4 .headline{left:0;top:443px;width:584px}
  .ad-a4 .title{font-size:40px;line-height:44px}
  .ad-a4 .sub{font-size:29px;line-height:36px}
  .ad-a4 .pitch{left:52px;top:591px;width:480px;font-size:21px;line-height:27px}
  .ad-a4 .contact{left:0;top:712px;width:584px;font-size:17px;line-height:30px}
  .ad-a4 .contact svg{width:14px;height:14px}

  /* 55 x 118 */
  .ad-tall .brand{left:0;top:18px;width:151px;font-size:22px}
  .ad-tall .photo{left:11px;top:54px;width:129px;height:91px}
  .ad-tall .headline{left:0;top:156px;width:151px}
  .ad-tall .title{font-size:15px;line-height:16px}
  .ad-tall .sub{font-size:11px;line-height:14px}
  .ad-tall .pitch{left:8px;top:218px;width:135px;font-size:8px;line-height:10.3px}
  .ad-tall .contact{left:0;top:274px;width:151px;font-size:6.5px;line-height:11.5px}
  .ad-tall .contact .row{gap:.6em}
  .ad-tall .contact svg{width:6px;height:6px}

  /* 176 x 118 */
  .ad-wide .brand{left:25px;top:16px;width:166px;font-size:26px}
  .ad-wide .photo{left:224px;top:53px;width:229px;height:203px}
  .ad-wide .headline{left:14px;top:66px;width:196px}
  .ad-wide .title{font-size:19px;line-height:20px}
  .ad-wide .sub{font-size:15px;line-height:18px}
  .ad-wide .pitch{left:14px;top:149px;width:196px;font-size:16px;line-height:21.5px}
  .ad-wide .contact{left:0;top:294px;width:480px;font-size:9.5px;line-height:12px}
  .ad-wide .contact .row{gap:1.2em}
  .ad-wide .contact svg{width:8px;height:8px}
</style>
</head>
<body>
<svg width="0" height="0" style="position:absolute" aria-hidden="true">
  <defs>
    <symbol id="icon-pin" viewBox="0 0 10 14"><path d="M5 0a5 5 0 0 0-5 5c0 3.5 5 9 5 9s5-5.5 5-9a5 5 0 0 0-5-5zm0 7a2 2 0 1 1 0-4 2 2 0 0 1 0 4z"/></symbol>
    <symbol id="icon-mail" viewBox="0 0 14 10"><path d="M0 0h14v1.2L7 6 0 1.2zM0 3v7h14V3L7 7.8z"/></symbol>
    <symbol id="icon-phone" viewBox="0 0 24 24"><path d="M6.6 10.8c1.4 2.8 3.8 5.1 6.6 6.6l2.2-2.2c.3-.3.7-.4 1-.2 1.1.4 2.3.6 3.6.6.6 0 1 .4 1 1V20c0 .6-.4 1-1 1C10.6 21 3 13.4 3 4c0-.6.4-1 1-1h3.5c.6 0 1 .4 1 1 0 1.3.2 2.5.6 3.6.1.3 0 .7-.2 1z"/></symbol>
  </defs>
</svg>

<main class="board">

  <!-- A4 -->
  <section class="ad ad-a4">
    <svg class="shapes" width="584" height="826" viewBox="0 0 584 826" aria-hidden="true">
      <circle cx="32" cy="48" r="102" fill="var(--orange)"/>
      <path d="M451 0H584V222H505A54 54 0 0 1 451 168Z" fill="var(--slate)"/>
      <g fill="none" stroke="var(--orange)" stroke-width="2">
        <circle cx="4" cy="491" r="70"/><circle cx="4" cy="491" r="57"/><circle cx="4" cy="491" r="43"/>
      </g>
      <g fill="var(--slate)">
        <circle cx="535" cy="452" r="1.7"/><circle cx="555" cy="452" r="1.7"/><circle cx="575" cy="452" r="1.7"/>
        <circle cx="535" cy="483" r="1.7"/><circle cx="555" cy="483" r="1.7"/><circle cx="575" cy="483" r="1.7"/>
        <circle cx="535" cy="514" r="1.7"/><circle cx="555" cy="514" r="1.7"/><circle cx="575" cy="514" r="1.7"/>
        <circle cx="535" cy="544" r="1.7"/><circle cx="555" cy="544" r="1.7"/><circle cx="575" cy="544" r="1.7"/>
        <circle cx="535" cy="575" r="1.7"/><circle cx="555" cy="575" r="1.7"/><circle cx="575" cy="575" r="1.7"/>
      </g>
      <path d="M0 600A87 87 0 0 1 87 687V826H0Z" fill="var(--slate)"/>
      <g fill="var(--orange)">
        <circle cx="13" cy="652" r="2"/><circle cx="44" cy="652" r="2"/><circle cx="74" cy="652" r="2"/><circle cx="104" cy="652" r="2"/>
        <circle cx="13" cy="672" r="2"/><circle cx="44" cy="672" r="2"/><circle cx="74" cy="672" r="2"/><circle cx="104" cy="672" r="2"/>
        <circle cx="13" cy="692" r="2"/><circle cx="44" cy="692" r="2"/><circle cx="74" cy="692" r="2"/><circle cx="104" cy="692" r="2"/>
      </g>
      <circle cx="506" cy="826" r="78" fill="var(--orange)"/>
      <g fill="none" stroke="var(--slate)" stroke-width="2">
        <path d="M495 826V729A89 89 0 0 1 673 729"/>
        <path d="M509 826V729A75 75 0 0 1 659 729"/>
        <path d="M522 826V729A62 62 0 0 1 646 729"/>
      </g>
      <g stroke="var(--slate)" stroke-width="1.5">
        <line x1="117" y1="566" x2="467" y2="566"/>
        <line x1="117" y1="693" x2="467" y2="693"/>
      </g>
    </svg>
    <div class="brand">TOLVEK</div>
    <div class="photo" role="img" aria-label="Foto: Pflegekraft hilft einem älteren Herrn im hellen Zimmer beim Aufstehen vom Bett"></div>
    <h1 class="headline"><span class="title">Moderne Pflege:</span><span class="sub">wirtschaftlich, nachhaltig</span><span class="sub">und zukunftssicher</span></h1>
    <p class="pitch">Steht Ihr Pflegedienst vor Herausforderungen?<br>Gemeinsam gestalten wir eine<br>zukunftssichere Lösung.</p>
    <div class="contact">
      <div class="row"><span class="item"><svg><use href="#icon-mail"/></svg>info@tolvek-beispiel.de</span><span class="item"><svg><use href="#icon-phone"/></svg>0555 91827364</span></div>
      <div class="row"><span class="item"><svg><use href="#icon-pin"/></svg>Rostock</span><span class="item"><svg><use href="#icon-pin"/></svg>Berlin</span></div>
      <div class="row"><span class="item"><svg><use href="#icon-pin"/></svg>und bundesweit tätig</span></div>
    </div>
  </section>

  <!-- 55,3 x 118 mm -->
  <section class="ad ad-tall">
    <svg class="shapes" width="151" height="321" viewBox="0 0 151 321" aria-hidden="true">
      <circle cx="14" cy="14" r="32" fill="var(--orange)"/>
      <g fill="var(--slate)">
        <circle cx="134" cy="4" r=".7"/><circle cx="141" cy="4" r=".7"/><circle cx="148" cy="4" r=".7"/>
        <circle cx="134" cy="14" r=".7"/><circle cx="141" cy="14" r=".7"/><circle cx="148" cy="14" r=".7"/>
        <circle cx="134" cy="24" r=".7"/><circle cx="141" cy="24" r=".7"/><circle cx="148" cy="24" r=".7"/>
        <circle cx="134" cy="34" r=".7"/><circle cx="141" cy="34" r=".7"/><circle cx="148" cy="34" r=".7"/>
      </g>
      <g fill="none" stroke="var(--orange)" stroke-width="1">
        <circle cx="151" cy="159" r="12"/><circle cx="151" cy="159" r="9"/>
        <circle cx="0" cy="228" r="13"/><circle cx="0" cy="228" r="10"/><circle cx="0" cy="228" r="7"/>
      </g>
      <path d="M0 268A19 19 0 0 1 19 287V321H0Z" fill="var(--slate)"/>
      <circle cx="124" cy="321" r="27" fill="var(--orange)"/>
      <g fill="none" stroke="var(--slate)" stroke-width="1">
        <path d="M128 321V290A23 23 0 0 1 174 290"/>
        <path d="M133 321V290A18 18 0 0 1 169 290"/>
        <path d="M138 321V290A13 13 0 0 1 164 290"/>
      </g>
      <g stroke="var(--slate)" stroke-width=".8">
        <line x1="5" y1="210" x2="145" y2="210"/>
        <line x1="5" y1="265" x2="145" y2="265"/>
      </g>
    </svg>
    <div class="brand">TOLVEK</div>
    <div class="photo" role="img" aria-label="Foto: Pflegekraft hilft einem älteren Herrn im hellen Zimmer beim Aufstehen vom Bett"></div>
    <h2 class="headline"><span class="title">Moderne Pflege:</span><span class="sub">wirtschaftlich, nachhaltig</span><span class="sub">und zukunftssicher</span></h2>
    <p class="pitch">Steht Ihr Pflegedienst vor<br>Herausforderungen?<br>Gemeinsam gestalten wir eine<br>zukunftssichere Lösung.</p>
    <div class="contact">
      <div class="row"><span class="item"><svg><use href="#icon-mail"/></svg>info@tolvek-beispiel.de</span><span class="item"><svg><use href="#icon-phone"/></svg>0555 91827364</span></div>
      <div class="row"><span class="item"><svg><use href="#icon-pin"/></svg>Rostock</span><span class="item"><svg><use href="#icon-pin"/></svg>Berlin</span></div>
      <div class="row"><span class="item"><svg><use href="#icon-pin"/></svg>und bundesweit tätig</span></div>
    </div>
  </section>

  <!-- 176 x 118 mm -->
  <section class="ad ad-wide">
    <svg class="shapes" width="480" height="321" viewBox="0 0 480 321" aria-hidden="true">
      <path d="M0 0H33V52A33 33 0 0 1 0 85Z" fill="var(--slate)"/>
      <g fill="var(--orange)">
        <circle cx="5" cy="4" r=".9"/><circle cx="14" cy="4" r=".9"/><circle cx="23" cy="4" r=".9"/><circle cx="40" cy="4" r=".9"/>
        <circle cx="5" cy="14" r=".9"/><circle cx="14" cy="14" r=".9"/><circle cx="23" cy="14" r=".9"/><circle cx="40" cy="14" r=".9"/>
        <circle cx="5" cy="24" r=".9"/><circle cx="14" cy="24" r=".9"/><circle cx="23" cy="24" r=".9"/><circle cx="40" cy="24" r=".9"/>
      </g>
      <g fill="var(--slate)">
        <circle cx="225" cy="10" r="1.2"/><circle cx="246" cy="10" r="1.2"/><circle cx="267" cy="10" r="1.2"/><circle cx="288" cy="10" r="1.2"/><circle cx="309" cy="10" r="1.2"/>
        <circle cx="225" cy="24" r="1.2"/><circle cx="246" cy="24" r="1.2"/><circle cx="267" cy="24" r="1.2"/><circle cx="288" cy="24" r="1.2"/><circle cx="309" cy="24" r="1.2"/>
        <circle cx="225" cy="38" r="1.2"/><circle cx="246" cy="38" r="1.2"/><circle cx="267" cy="38" r="1.2"/><circle cx="288" cy="38" r="1.2"/><circle cx="309" cy="38" r="1.2"/>
      </g>
      <circle cx="453" cy="23" r="49" fill="var(--orange)"/>
      <g fill="var(--orange)">
        <circle cx="459" cy="124" r="1.3"/><circle cx="474" cy="124" r="1.3"/>
        <circle cx="459" cy="148" r="1.3"/><circle cx="474" cy="148" r="1.3"/>
        <circle cx="459" cy="170" r="1.3"/><circle cx="474" cy="170" r="1.3"/>
        <circle cx="459" cy="194" r="1.3"/><circle cx="474" cy="194" r="1.3"/>
      </g>
      <g fill="none" stroke="var(--orange)" stroke-width="1.3">
        <circle cx="0" cy="293" r="28"/><circle cx="0" cy="293" r="22"/><circle cx="0" cy="293" r="16"/>
      </g>
      <circle cx="450" cy="321" r="30" fill="var(--orange)"/>
      <g fill="none" stroke="var(--slate)" stroke-width="1.2">
        <path d="M447 321V286A33 33 0 0 1 513 286"/>
        <path d="M454 321V286A26 26 0 0 1 506 286"/>
        <path d="M461 321V286A19 19 0 0 1 499 286"/>
      </g>
      <g stroke="var(--slate)" stroke-width="1">
        <line x1="20" y1="137" x2="197" y2="137"/>
        <line x1="43" y1="280" x2="427" y2="280"/>
      </g>
    </svg>
    <div class="brand">TOLVEK</div>
    <div class="photo" role="img" aria-label="Foto: Pflegekraft hilft einem älteren Herrn im hellen Zimmer beim Aufstehen vom Bett"></div>
    <h2 class="headline"><span class="title">Moderne Pflege:</span><span class="sub">wirtschaftlich, nachhaltig</span><span class="sub">und zukunftssicher</span></h2>
    <p class="pitch">Steht Ihr Pflegedienst<br>vor Herausforderungen?<br>Gemeinsam gestalten<br>wir eine zukunftssichere<br>Lösung.</p>
    <div class="contact">
      <div class="row"><span class="item"><svg><use href="#icon-mail"/></svg>info@tolvek-beispiel.de</span><span class="item"><svg><use href="#icon-phone"/></svg>0555 91827364</span><span class="item"><svg><use href="#icon-pin"/></svg>Rostock</span><span class="item"><svg><use href="#icon-pin"/></svg>Berlin</span><span class="item"><svg><use href="#icon-pin"/></svg>und bundesweit tätig</span></div>
    </div>
  </section>

</main>
</body>
</html>
```